Gobal construction supply company needs new business card design

I need a business card design for my global supply company using an existing logo. i will be looking to print these on rounded corner cards with the black background version of my logo on the back. on the front white background, my logo again and my simple details.

```html
<!DOCTYPE html>
<html lang="en">
<head>
<meta charset="UTF-8">
<title>Kestrel Build Supply – Business Cards</title>
<link href="https://fonts.googleapis.com/css2?family=Montserrat:wght@500;600;700&display=swap" rel="stylesheet">
<style>
  :root {
    --backdrop: #3b3b3d;
    --card-black: #121212;
    --card-white: #ffffff;
    --brand-red: #e0000b;
    --ink: #1a1a1a;
    --emboss: #3a3a3a;
  }
  * { box-sizing: border-box; margin: 0; padding: 0; }
  html, body {
    width: 1200px; height: 1000px; overflow: hidden;
    background: var(--backdrop);
    font-family: "Montserrat", Arial, sans-serif;
  }
  .canvas { position: relative; width: 1200px; height: 1000px; }

  .card {
    position: absolute;
    width: 720px; height: 410px;
    border-radius: 28px;
    overflow: hidden;
    box-shadow: 0 18px 40px rgba(0,0,0,.45);
  }

  .wordmark {
    font-weight: 700; letter-spacing: .5px; line-height: 1.1;
    text-transform: uppercase; white-space: nowrap;
  }

  /* Back of card */
  .card-back {
    left: 360px; top: 60px;
    background: var(--card-black);
    display: flex; align-items: center; justify-content: center;
  }
  .card-back .wordmark { color: var(--emboss); font-size: 38px; }

  /* Front of card */
  .card-front {
    left: 120px; top: 530px;
    background: var(--card-white);
    display: flex; align-items: center;
  }
  .card-front .red-band {
    position: absolute; left: 0; right: 0; bottom: 0;
    height: 44px; background: var(--brand-red);
  }
  .brand-block {
    width: 400px; padding-left: 30px; padding-right: 20px; padding-bottom: 40px;
    display: flex; justify-content: center;
  }
  .card-front .wordmark { color: var(--ink); font-size: 24px; }

  .divider {
    width: 2px; height: 220px; background: var(--brand-red);
    margin-bottom: 40px; flex: none;
  }
  .details { padding-left: 24px; padding-bottom: 40px; color: var(--ink); }
  .person-name { color: var(--brand-red); font-weight: 700; font-size: 22px; }
  .person-title { font-weight: 500; font-size: 15px; margin-bottom: 22px; }
  .address { font-weight: 500; font-size: 15px; line-height: 1.35; margin-bottom: 12px; }
  .contact-list { list-style: none; font-weight: 600; font-size: 17px; line-height: 1.5; }
  .contact-list li { display: flex; align-items: center; gap: 8px; white-space: nowrap; }
  .contact-list svg { width: 14px; height: 14px; flex: none; }
</style>
</head>
<body>
<div class="canvas">

  <section class="card card-back" aria-label="Card back">
    <span class="wordmark">Kestrel Build Supply</span>
  </section>

  <section class="card card-front" aria-label="Card front">
    <div class="brand-block">
      <span class="wordmark">Kestrel Build Supply</span>
    </div>

    <div class="divider"></div>

    <div class="details">
      <p class="person-name">MARCUS HALE</p>
      <p class="person-title">Managing Director</p>
      <p class="address">2150 Brennan Avenue,<br>Tulsa, OK 74105</p>
      <ul class="contact-list">
        <li>
          <svg viewBox="0 0 24 24" fill="var(--brand-red)"><path d="M6.6 10.8a15.1 15.1 0 0 0 6.6 6.6l2.2-2.2a1 1 0 0 1 1-.25 11.4 11.4 0 0 0 3.6.57 1 1 0 0 1 1 1V20a1 1 0 0 1-1 1A17 17 0 0 1 3 4a1 1 0 0 1 1-1h3.5a1 1 0 0 1 1 1c0 1.25.2 2.45.57 3.57a1 1 0 0 1-.25 1z"/></svg>
          +1 (555) 014 2290
        </li>
        <li>
          <svg viewBox="0 0 24 24" fill="none" stroke="var(--brand-red)" stroke-width="2.4"><rect x="6" y="2" width="12" height="20" rx="2"/><line x1="11" y1="18" x2="13" y2="18"/></svg>
          +1 (555) 014 2291
        </li>
        <li>
          <svg viewBox="0 0 24 24" fill="var(--brand-red)"><path d="M2 5h20v14H2z"/><path d="M2 5l10 8 10-8" fill="none" stroke="#fff" stroke-width="2"/></svg>
          marcus@kestrelbuild.com
        </li>
        <li>
          <svg viewBox="0 0 24 24" fill="none" stroke="var(--brand-red)" stroke-width="2.2"><circle cx="12" cy="12" r="10"/><ellipse cx="12" cy="12" rx="4" ry="10"/><line x1="2" y1="12" x2="22" y2="12"/></svg>
          www.kestrelbuild.com
        </li>
      </ul>
    </div>

    <div class="red-band"></div>
  </section>

</div>
</body>
</html>
```